KRV Business Card

Looking for a business card for my restaurant group I own. Four different concepts:

Copperfield Alehouse
Bristow Alehouse
Tanager's Stone Hearth Kitchen
Pellston Patty Company

Card doesn't need to include all the logos.

```html
<!DOCTYPE html>
<html lang="en">
<head>
<meta charset="utf-8">
<title>KRV Business Card</title>
<link href="https://fonts.googleapis.com/css2?family=Lato:wght@400;700;900&display=swap" rel="stylesheet">
<style>
  :root {
    --backdrop: #3a332f;
    --card: #0e0e0e;
    --card-edge: #1c1c1c;
    --gold: #c9a55c;
    --silver: #b9b9b9;
    --white: #f2f2f2;
    --muted: #9a9a9a;
    --divider: #2e2e2e;
  }
  * { margin: 0; padding: 0; box-sizing: border-box; }
  html, body { width: 1200px; height: 844px; overflow: hidden; }
  body {
    background: var(--backdrop);
    font-family: "Lato", Arial, sans-serif;
    position: relative;
  }
  .card {
    position: absolute;
    top: 273px;
    width: 520px;
    height: 298px;
    background: var(--card);
    border: 1px solid var(--card-edge);
    box-shadow: 0 10px 30px rgba(0,0,0,.45);
  }
  .card--front { left: 60px; }
  .card--back { left: 620px; }

  /* front */
  .brand {
    position: absolute;
    left: 40px;
    top: 88px;
    width: 220px;
  }
  .brand__mark {
    color: var(--gold);
    font-weight: 900;
    font-size: 44px;
    letter-spacing: 4px;
    line-height: 1;
  }
  .brand__name {
    margin-top: 14px;
    color: var(--gold);
    font-weight: 700;
    font-size: 30px;
    letter-spacing: 5px;
    line-height: 1;
  }
  .brand__tagline {
    margin-top: 6px;
    color: var(--muted);
    font-size: 14px;
    letter-spacing: 3.4px;
    text-transform: uppercase;
  }
  .divider {
    position: absolute;
    left: 272px;
    top: 60px;
    width: 1px;
    height: 178px;
    background: var(--divider);
  }
  .contact {
    position: absolute;
    left: 292px;
    top: 64px;
    color: var(--muted);
    font-size: 14px;
    line-height: 1.45;
  }
  .contact__name {
    color: var(--gold);
    font-weight: 900;
    font-size: 17px;
    letter-spacing: .5px;
    text-transform: uppercase;
  }
  .contact__title { margin-bottom: 2px; }
  .contact__row { display: flex; align-items: center; gap: 7px; }
  .contact__icon { width: 10px; height: 10px; fill: var(--gold); flex: none; }
  .contact__address { margin-top: 8px; }

  /* back */
  .back-mark {
    position: absolute;
    left: 0; right: 0;
    top: 82px;
    text-align: center;
    color: var(--silver);
    font-weight: 900;
    font-size: 56px;
    letter-spacing: 6px;
    line-height: 1;
  }
  .concepts {
    position: absolute;
    left: 0; right: 0;
    top: 196px;
    text-align: center;
    color: var(--white);
    font-size: 11px;
    letter-spacing: .6px;
    line-height: 1.6;
    text-transform: uppercase;
  }
  .concepts__sep { margin: 0 6px; color: var(--muted); }
</style>
</head>
<body>
  <section class="card card--front">
    <div class="brand">
      <div class="brand__mark">KRV</div>
      <div class="brand__name">KESTREL</div>
      <div class="brand__tagline">River Ventures</div>
    </div>
    <div class="divider"></div>
    <div class="contact">
      <div class="contact__name">Marcus Hale</div>
      <div class="contact__title">Managing Director</div>
      <div class="contact__row">
        <svg class="contact__icon" viewBox="0 0 10 10"><path d="M2 0l2 2-1 1.5c.8 1.5 2 2.7 3.5 3.5L8 6l2 2-1.5 2C4 10 0 6 0 1.5z"/></svg>
        044-555 019 274
      </div>
      <div class="contact__row">
        <svg class="contact__icon" viewBox="0 0 10 10"><path d="M0 2h10v6H0z M0 2l5 3.5L10 2" stroke="#0e0e0e" stroke-width=".8"/></svg>
        info@kestrelriver.com
      </div>
      <div class="contact__row">
        <svg class="contact__icon" viewBox="0 0 10 10"><circle cx="5" cy="5" r="5"/></svg>
        www.kestrelriver.com
      </div>
      <div class="contact__address">421, Address line here,<br>45452,Country Name</div>
    </div>
  </section>

  <section class="card card--back">
    <div class="back-mark">KRV</div>
    <div class="concepts">
      <div>Copperfield Alehouse<span class="concepts__sep">|</span>Bristow Alehouse</div>
      <div>Tanager's Stone Hearth Kitchen<span class="concepts__sep">|</span>Pellston Patty Company</div>
    </div>
  </section>
</body>
</html>
```